Website for new child psychology practice

New clinical psychology practice in NSW Australia, specialising in work with children, adolescents and families. I would like to feature the colours in the logo, which was recently designed by pixelharbor designer Odette.
I am seeking a professional looking page, which is easy to navigate and is colourful and playful but not childish.
Target Market(s)
Parents and professionals
Industry/Entity Type
Health
Coding
Coded - Design and coding required
Number of Pages Required
1 page
Font styles to use
Serif
Requirements
Must have
- Pages for 'About us' 'Services' 'Fees and information' 'Contact us'
Should not have
- Childish stock photos

```html
<!DOCTYPE html>
<html lang="en">
<head>
<meta charset="utf-8">
<title>Dr Clara Hayes – Clinical Psychologist</title>
<link rel="stylesheet" href="https://fonts.googleapis.com/css2?family=Cinzel:wght@600;700&family=Roboto:wght@400;500;700&display=swap">
<style>
:root{
  --magenta:#a62a93;
  --magenta-deep:#9b2389;
  --pink:#cd6fb2;
  --gold:#d9a65a;
  --ink:#1f1f1f;
  --body:#6a6a6a;
  --line:#e4e4e4;
  --footer:#050505;
  --footer-text:#ffffff;
}
*{box-sizing:border-box;margin:0;padding:0}
html,body{width:1200px;height:4229px;overflow:hidden}
body{position:relative;background:#fff;font-family:'Roboto',sans-serif;color:var(--ink)}
.abs{position:absolute}
.serif{font-family:'Cinzel',serif;font-weight:700}
.photo{position:absolute}
.btn{position:absolute;display:flex;align-items:center;justify-content:center;border-radius:20px;background:var(--magenta);color:#fff;font-size:13px;font-weight:700;text-transform:uppercase}
.rule{position:absolute;height:3px;background:var(--gold)}
p.copy{font-size:13px;line-height:21.5px;color:var(--body)}

/* header */
.brand{left:112px;top:22px;display:flex;align-items:center;gap:10px}
.brand-dot{width:36px;height:36px;border-radius:50%;background:var(--magenta)}
.brand-name{font-family:'Roboto',sans-serif;font-weight:500;font-size:22px;color:var(--ink);letter-spacing:.5px}
.nav{left:456px;top:36px;font-size:13.5px}
.nav a{position:absolute;white-space:nowrap;color:#333;text-decoration:none}
.nav a.active{color:var(--magenta)}

/* hero */
.hero-title{left:112px;top:236px;font-size:50px;letter-spacing:1px}
.hero-sub{left:112px;top:298px;font-size:20px;color:var(--gold);font-family:'Cinzel',serif;font-weight:600}
.hero-text{left:112px;top:335px;width:460px}
.dots{left:112px;top:574px;display:flex;align-items:center}
.dot{width:22px;height:22px;border-radius:50%;background:#eee;border:1px solid #ddd;font-size:9px;display:flex;align-items:center;justify-content:center;color:#555}
.dot.on{background:var(--gold);color:#fff;border-color:var(--gold)}

/* services */
.section-title{left:0;width:1200px;text-align:center;font-size:42px}
.svc{position:absolute;top:844px;width:304px;height:424px;border-radius:12px;background:var(--pink);color:#fff;text-align:center;padding:38px 36px 0}
.svc.feature{background:var(--magenta)}
.svc svg{display:block;margin:0 auto}
.svc h3{font-size:21px;font-weight:500;margin:22px 0 16px}
.svc p{font-size:12.5px;line-height:21.5px}
.svc .outline{display:inline-flex;margin-top:20px;height:40px;width:144px;align-items:center;justify-content:center;border:2px solid #fff;border-radius:20px;font-size:12.5px;font-weight:700}
.arrow{position:absolute;width:44px;height:44px;border-radius:50%;border:1.5px solid #555;display:flex;align-items:center;justify-content:center}

/* fees */
.fee{position:absolute;width:470px;height:206px;border:1px solid var(--line);border-radius:4px}
.fee .photo{left:12px;top:12px;width:184px;height:184px;border-radius:4px}
.fee h4{position:absolute;left:220px;top:30px;font-size:21px;font-weight:500}
.fee p{position:absolute;left:220px;top:70px;width:230px;font-size:12.5px;line-height:21px;color:var(--body)}
.fee .price{position:absolute;left:222px;top:146px;font-size:30px;font-weight:700;color:var(--magenta);text-decoration:underline;text-underline-offset:5px}

/* contact */
.contact-panel{left:112px;top:2673px;width:487px;height:442px;background:var(--magenta-deep)}
.field{position:absolute;background:rgba(255,255,255,.18);border:1px solid rgba(255,255,255,.35);color:#fff;font-size:13px;padding:10px 12px}

/* testimonial */
.testi-title{left:108px;top:3324px;font-size:44px;line-height:52px}
.stars{left:110px;top:3496px;color:var(--gold);font-size:17px;letter-spacing:4px}

/* footer */
.footer{left:0;top:3831px;width:1200px;height:398px;background:var(--footer)}
.f-item{position:absolute;display:flex;align-items:center;gap:12px;font-size:14px;line-height:17px;color:var(--footer-text)}
.f-icon{width:40px;height:40px;border-radius:50%;background:#fff;flex:none;display:flex;align-items:center;justify-content:center}
.f-head{position:absolute;font-size:20px;font-weight:700;color:var(--footer-text)}
.f-links{position:absolute;left:539px;top:3981px;font-size:14px;line-height:25.5px;list-style:none;color:var(--footer-text)}
.f-links li::before{content:"»";color:var(--gold);margin-right:16px}
.f-copy{left:0;top:4177px;width:1200px;text-align:center;font-size:13px;color:var(--footer-text)}
</style>
</head>
<body>

<!-- header -->
<div class="abs brand"><span class="brand-dot"></span><span class="brand-name">DR CLARA HAYES</span></div>
<nav class="abs nav">
  <a class="active" style="left:0">Home</a>
  <a style="left:64px">About us</a>
  <a style="left:147px">Services</a>
  <a style="left:227px">Fees and information</a>
  <a style="left:385px">Contact us</a>
</nav>
<div class="btn" style="left:949px;top:26px;width:140px;height:36px">Get in touch</div>

<!-- hero -->
<h1 class="abs serif hero-title">Dr.Clara Hayes</h1>
<div class="abs hero-sub">Clinical Psychologist</div>
<p class="abs copy hero-text">Lorem ipsum dolor sit amet, consectetur adipiscing elit, sed do eiusmod tempor incididunt ut labore et dolore magna aliqua.</p>
<div class="btn" style="left:112px;top:394px;width:138px;height:36px">Get started</div>
<div class="abs dots">
  <span class="dot on">1</span><span style="width:60px;height:1px;background:#ccc;margin:0 6px"></span>
  <span class="dot">2</span><span style="width:12px"></span><span class="dot">3</span>
</div>

<div class="photo" role="img" aria-label="Distressed young woman holding her head" style="left:665px;top:138px;width:102px;height:102px;border-radius:50%;background:linear-gradient(135deg,#9a9a9a,#5d5d5d)"></div>
<div class="photo" role="img" aria-label="Therapy session with a client on a sofa" style="left:829px;top:121px;width:371px;height:360px;border-radius:160px 0 0 0;background:linear-gradient(135deg,#8a7a6a,#4e4a4c 60%,#6c5a4a)"></div>
<div class="photo" style="left:722px;top:294px;width:91px;height:80px;border-radius:50px 0 0 0;background:var(--gold)"></div>
<div class="photo" role="img" aria-label="Smiling psychologist with a client" style="left:614px;top:392px;width:199px;height:179px;border-radius:0 0 0 90px;background:linear-gradient(135deg,#d8d6d2,#b5aea4)"></div>
<div class="photo" role="img" aria-label="Child playing with toys during therapy" style="left:829px;top:497px;width:140px;height:125px;border-radius:0 0 70px 0;background:linear-gradient(135deg,#c9c6c4,#c08a5a)"></div>
<div class="photo" role="img" aria-label="Counselling conversation" style="left:1025px;top:497px;width:101px;height:101px;border-radius:50%;background:linear-gradient(135deg,#9fb0c2,#66788d)"></div>

<!-- services -->
<div class="rule" style="left:558px;top:748px;width:84px"></div>
<h2 class="abs serif section-title" style="top:768px">Our Services</h2>

<div class="arrow" style="left:34px;top:1029px"><svg width="12" height="12" viewBox="0 0 12 12"><path d="M8 1 3 6l5 5" fill="none" stroke="#333" stroke-width="1.6"/></svg></div>
<div class="arrow" style="left:1122px;top:1029px"><svg width="12" height="12" viewBox="0 0 12 12"><path d="M4 1l5 5-5 5" fill="none" stroke="#333" stroke-width="1.6"/></svg></div>

<div class="svc" style="left:112px">
  <svg width="72" height="72" viewBox="0 0 72 72" fill="none" stroke="#fff" stroke-width="2"><circle cx="28" cy="18" r="10"/><circle cx="46" cy="30" r="8"/><path d="M10 62V46a12 12 0 0 1 12-12h12M34 62V50a10 10 0 0 1 10-10h4a10 10 0 0 1 10 10v12M8 56l28 6 28-6"/></svg>
  <h3>Lorem ipsum dolor</h3>
  <p>Lorem ipsum dolor sit amet, consect etur adipiscing elit, sed do eiusmod tempor incididunt ut labore et dolore magna aliqua. Lorem ipsum dolor sit amet, consectetur adipiscing elit, sed do eiusmod tempor incididunt ut et dolore magna aliqua.</p>
  <span class="outline">LEARN MORE</span>
</div>
<div class="svc feature" style="left:448px">
  <svg width="72" height="72" viewBox="0 0 72 72" fill="none" stroke="#fff" stroke-width="2"><circle cx="26" cy="16" r="9"/><circle cx="46" cy="16" r="9"/><path d="M12 64V40a10 10 0 0 1 10-10h8a10 10 0 0 1 10 10v24M32 64V40a10 10 0 0 1 10-10h8a10 10 0 0 1 10 10v24M22 48h8M42 48h8"/></svg>
  <h3>Lorem ipsum dolor</h3>
  <p>Lorem ipsum dolor sit amet, consect etur adipiscing elit, sed do eiusmod tempor incididunt ut labore et dolore magna aliqua. Lorem ipsum dolor sit amet, consectetur adipiscing elit, sed do eiusmod tempor incididunt ut et dolore magna aliqua.</p>
  <span class="outline">LEARN MORE</span>
</div>
<div class="svc" style="left:785px">
  <svg width="72" height="72" viewBox="0 0 72 72" fill="none" stroke="#fff" stroke-width="2"><circle cx="16" cy="14" r="6"/><circle cx="56" cy="14" r="6"/><circle cx="36" cy="22" r="5"/><path d="M16 22v40M56 22v40M8 26l8 8 8-8M48 26l8 8 8-8M36 50l-8-8a5 5 0 0 1 8-6 5 5 0 0 1 8 6z"/></svg>
  <h3>Lorem ipsum dolor</h3>
  <p>Lorem ipsum dolor sit amet, consect etur adipiscing elit, sed do eiusmod tempor incididunt ut labore et dolore magna aliqua. Lorem ipsum dolor sit amet, consectetur adipiscing elit, sed do eiusmod tempor incididunt ut et dolore magna aliqua.</p>
  <span class="outline">LEARN MORE</span>
</div>

<!-- about -->
<div class="photo" role="img" aria-label="Smiling psychologist seated on a sofa holding a notebook" style="left:0;top:1392px;width:608px;height:449px;background:linear-gradient(100deg,#cbb89c 0%,#bfa98c 40%,#5f7f9c 62%,#3d6a94 72%,#e9e5df 100%);clip-path:polygon(0 37%,43% 37%,43% 0,78% 0,78% 100%,0 100%)"></div>
<div class="rule" style="left:621px;top:1414px;width:82px"></div>
<h2 class="abs serif" style="left:619px;top:1436px;font-size:42px">About Us</h2>
<p class="abs copy" style="left:621px;top:1498px;width:468px;text-align:justify">Lorem ipsum dolor sit amet, consectetur adipiscing elit, sed do eiusmod tempor incididunt ut labore et dolore magna aliqua. Ut enim ad minim veniam, quis nostrud exercitation ullamco laboris nisi ut aliquip ex ea commodo consequat. Duis aute irure dolor in reprehenderit in voluptate velit esse cillum dolore eu fugiat nulla pariatur. Excepteur sint occaecat cupidatat non proident, sunt in culpa qui officia deserunt mollit anim id est laborum. Lorem ipsum dolor sit amet, consectetur adipiscing elit, sed do eiusmod tempor incididunt ut labore et dolore magna aliqua. Ut enim ad minim veniam, quis nostrud exercitation ullamco laboris nisi ut aliquip ex ea commodo consequat. Duis aute irure dolor in reprehenderit in voluptate velit esse cillum dolore eu fugiat nulla pariatur. Excepteur sint occaecat cupidatat sunt in culpa qui officia deserunt mollit anim id est laborum.</p>
<div class="btn" style="left:619px;top:1796px;width:140px;height:37px">Learn more</div>

<!-- fees -->
<div class="rule" style="left:558px;top:1948px;width:84px"></div>
<h2 class="abs serif section-title" style="top:1970px">Fees and Information</h2>

<div class="fee" style="left:112px;top:2049px">
  <div class="photo" role="img" aria-label="Psychologist taking notes with a client" style="background:linear-gradient(135deg,#d9d3c8,#8f97a3)"></div>
  <h4>Lorem ipsum dolor</h4><p>Lorem ipsum dolor sit amet, conse ctetur adipiscing elit, sed do eiusmod tempor incididunt ut labore</p><span class="price">$25.00</span>
</div>
<div class="fee" style="left:619px;top:2049px">
  <div class="photo" role="img" aria-label="Client talking in a bright counselling room" style="background:linear-gradient(135deg,#cfd3d6,#8a7262)"></div>
  <h4>Lorem ipsum dolor</h4><p>Lorem ipsum dolor sit amet, conse ctetur adipiscing elit, sed do eiusmod tempor incididunt ut labore</p><span class="price">$25.00</span>
</div>
<div class="fee" style="left:112px;top:2289px">
  <div class="photo" role="img" aria-label="Group therapy conversation" style="background:linear-gradient(135deg,#d7d2c8,#6d6156)"></div>
  <h4>Lorem ipsum dolor</h4><p>Lorem ipsum dolor sit amet, conse ctetur adipiscing elit, sed do eiusmod tempor incididunt ut labore</p><span class="price">$25.00</span>
</div>
<div class="fee" style="left:619px;top:2289px">
  <div class="photo" role="img" aria-label="Woman speaking with a therapist" style="background:linear-gradient(135deg,#8a7f76,#4a4450)"></div>
  <h4>Lorem ipsum dolor</h4><p>Lorem ipsum dolor sit amet, conse ctetur adipiscing elit, sed do eiusmod tempor incididunt ut labore</p><span class="price">$25.00</span>
</div>

<!-- contact -->
<div class="photo" role="img" aria-label="Young girl hugging a teddy bear on a red chair" style="left:0;top:2594px;width:1200px;height:600px;background:linear-gradient(100deg,#d8b894 0%,#e9d2b6 45%,#e6c8a8 62%,#c98b66 78%,#d4502e 100%)"></div>
<div class="abs contact-panel"></div>
<div class="abs" style="left:315px;top:2719px;width:82px;height:3px;background:#fff"></div>
<h2 class="abs serif" style="left:112px;top:2736px;width:487px;text-align:center;font-size:42px;color:#fff">Get In Touch</h2>
<div class="field" style="left:148px;top:2803px;width:198px;height:37px">Name</div>
<div class="field" style="left:363px;top:2803px;width:198px;height:37px">Phone</div>
<div class="field" style="left:148px;top:2855px;width:413px;height:38px">Email</div>
<div class="field" style="left:148px;top:2906px;width:413px;height:99px">Message</div>
<div class="btn" style="left:284px;top:3023px;width:141px;height:38px;background:var(--gold)">Submit</div>

<!-- testimonial -->
<div class="rule" style="left:108px;top:3302px;width:82px"></div>
<h2 class="abs serif testi-title">Happy Patient Says<br>Something About<br>Dr.Clara Hayes</h2>
<div class="abs stars">★★★★★</div>
<p class="abs copy" style="left:110px;top:3530px;width:460px">Lorem ipsum dolor sit amet, consectetur adipiscing elit, sed do eiusmod tempor incididunt ut labore et dolore magna aliqua. Ut enim ad minim veniam, quis nostrud exercitation ullamco laboris nisi ut aliquip ex ea commodo consequat. Duis aute irure dolor in reprehenderit in voluptate velit esse cillum dolore eu fugiat nulla pariatur.</p>
<div class="photo" role="img" aria-label="Client portrait" style="left:112px;top:3657px;width:68px;height:67px;background:linear-gradient(135deg,#d6d0c8,#9a8e84)"></div>
<div class="abs" style="left:198px;top:3664px;font-size:21px;font-weight:500">John Doe</div>
<div class="abs" style="left:198px;top:3694px;font-size:12.5px;color:#444">Company name</div>
<svg class="abs" style="left:514px;top:3686px" width="60" height="20" viewBox="0 0 60 20" fill="none" stroke-width="2"><path d="M11 3 4 10l7 7" stroke="#bbb"/><path d="M49 3l7 7-7 7" stroke="#a62a93"/></svg>
<div class="photo" style="left:603px;top:3575px;width:84px;height:92px;border-radius:50%;background:var(--gold)"></div>
<div class="photo" role="img" aria-label="Therapist and client talking in a sunlit room" style="left:645px;top:3304px;width:444px;height:420px;background:linear-gradient(180deg,#efeae3 0%,#e2d6c4 60%,#c9a24e 100%)"></div>

<!-- footer -->
<div class="abs footer"></div>
<div class="abs brand" style="top:3914px"><span class="brand-dot"></span><span class="brand-name" style="color:#fff;font-size:25px">DR CLARA HAYES</span></div>
<div class="f-item" style="left:111px;top:3987px"><span class="f-icon"><svg width="14" height="16" viewBox="0 0 14 16"><path d="M7 0a6 6 0 0 0-6 6c0 4.5 6 10 6 10s6-5.5 6-10a6 6 0 0 0-6-6zm0 8.5A2.5 2.5 0 1 1 7 3.5a2.5 2.5 0 0 1 0 5z" fill="#a62a93"/></svg></span><span>123, Lorem ipsum dolor sit<br>amet, consec</span></div>
<div class="f-item" style="left:111px;top:4047px"><span class="f-icon"><svg width="16" height="12" viewBox="0 0 16 12"><rect width="16" height="12" rx="1.5" fill="#a62a93"/><path d="M1 1.5l7 5 7-5" fill="none" stroke="#fff" stroke-width="1.4"/></svg></span><span>Email :<br>info@companyname.com</span></div>
<div class="f-item" style="left:111px;top:4105px"><span class="f-icon"><svg width="14" height="14" viewBox="0 0 14 14"><path d="M3 0l2.5 3.5-1.5 1.8a8 8 0 0 0 4.7 4.7L10.5 8.5 14 11l-1.5 2.5C6 14 0 8 .5 1.5z" fill="#a62a93"/></svg></span><span>Phone :<br>+1 888 888 8888</span></div>

<div class="f-head" style="left:539px;top:3924px">Quick Links</div>
<ul class="f-links"><li>Home</li><li>About us</li><li>Services</li><li>Fees and information</li><li>Contact us</li></ul>

<div class="f-head" style="left:775px;top:3924px">Subscribe to Our Newsletter</div>
<div class="abs" style="left:775px;top:3969px;width:314px;height:41px;background:#fff;border-radius:4px;display:flex;align-items:center;gap:10px;padding-left:16px;font-size:13px;color:#888">
  <svg width="14" height="10" viewBox="0 0 14 10"><rect width="14" height="10" rx="1" fill="#d9a65a"/><path d="M1 1l6 4 6-4" fill="none" stroke="#fff"/></svg>Email address</div>
<div class="btn" style="left:775px;top:4026px;width:141px;height:36px">Submit</div>

<div class="abs" style="left:355px;top:4133px;width:734px;height:1px;background:#555"></div>
<div class="abs f-copy">© Copyrights 2024 | All Rights Reserved</div>

</body>
</html>
```